Veltrane Group Business Card Design

The CEO is looking for a new trendy look for his business card.
You can stay with current branding or come up with something new/creative. It can be 3D, including Medical Office buildings. You can use our logo in a variety of colors. Please include name, title, company name, company website, email address, cell number

Target Market(s)

Real Estate Development and Construction

Industry/Entity Type

Health care real estate

Contact Information for Business Card

Rohesh Kamdar, CEO M-604.781.2249 E-roheshkamdar@veltrane.com Address:4180 Lindqvist Ave, Tampa, FL 33482 www.veltrane.com

Font styles to use
Other font styles liked:
• Be creative

Requirements
Must have
• Creative, trendy look
Nice to have
• Please go to our website to get a feel- www. veltrane.com
Should not have
• small fonts

```html
<!DOCTYPE html>
<html lang="en">
<head>
<meta charset="utf-8">
<title>Veltrane Group Business Card</title>
<link href="https://fonts.googleapis.com/css2?family=Montserrat:wght@400;700;800&display=swap" rel="stylesheet">
<style>
  :root {
    --stage: #2a2c30;
    --ink: #0d0d0d;
    --paper: #ffffff;
    --muted: #d9d9d9;
    --grey: #5a5a5a;
  }
  * { margin: 0; padding: 0; box-sizing: border-box; }
  html, body { width: 1200px; height: 900px; overflow: hidden; }
  body {
    background: var(--stage);
    font-family: "Montserrat", Arial, sans-serif;
    position: relative;
  }
  .card {
    position: absolute;
    width: 520px;
    height: 300px;
    border-radius: 20px;
    overflow: hidden;
  }
  .card-front { left: 50px; top: 300px; background: var(--paper); }
  .card-back { left: 630px; top: 300px; background: var(--ink); }
  .wave { position: absolute; inset: 0; width: 100%; height: 100%; }
  .holder { position: absolute; left: 32px; top: 28px; color: var(--ink); }
  .holder-name { font-weight: 700; font-size: 20px; letter-spacing: 0.2px; }
  .holder-title { font-weight: 400; font-size: 12px; color: var(--grey); margin-top: 2px; }
  .contact {
    position: absolute;
    left: 28px;
    bottom: 26px;
    list-style: none;
    color: var(--muted);
    font-size: 12px;
    line-height: 1.35;
  }
  .contact li { display: flex; align-items: flex-start; gap: 8px; margin-top: 5px; }
  .contact svg { width: 12px; height: 12px; flex: none; margin-top: 2px; }
  .contact .address { padding-left: 20px; }
  .wordmark {
    position: absolute;
    font-weight: 800;
    line-height: 0.95;
    text-align: right;
  }
  .card-front .wordmark { right: 36px; top: 112px; font-size: 40px; color: var(--ink); }
  .card-back .wordmark {
    left: 0; right: 0; top: 0; bottom: 0;
    display: flex; flex-direction: column; align-items: center; justify-content: center;
    font-size: 54px; color: var(--paper); text-align: center;
  }
</style>
</head>
<body>
  <section class="card card-front">
    <svg class="wave" viewBox="0 0 520 300" aria-hidden="true">
      <path d="M0,78 C140,62 220,100 262,168 C300,232 360,276 520,286" fill="none" stroke="#0d0d0d" stroke-width="5"/>
      <path d="M0,96 C125,86 205,118 242,182 C278,246 336,290 470,300 L0,300 Z" fill="#0d0d0d"/>
      <path d="M0,112 C118,104 192,132 226,192 C260,252 312,292 420,300" fill="none" stroke="#ffffff" stroke-width="4"/>
    </svg>
    <div class="holder">
      <div class="holder-name">Rohesh Kamdar</div>
      <div class="holder-title">CEO</div>
    </div>
    <ul class="contact">
      <li class="address">4180 Lindqvist Ave,<br>Tampa, FL 33482</li>
      <li><svg viewBox="0 0 12 12"><path d="M2.5 1 L4.5 1 L5 3.5 L3.8 4.5 C4.5 6 6 7.5 7.5 8.2 L8.5 7 L11 7.5 L11 9.5 C11 10.5 10 11 9 11 C4.5 10.5 1.5 7.5 1 3 C1 2 1.5 1 2.5 1Z" fill="#d9d9d9"/></svg>604.781.2249</li>
      <li><svg viewBox="0 0 12 12"><rect x="1" y="2.5" width="10" height="7" rx="1" fill="#d9d9d9"/><path d="M1.5 3 L6 6.5 L10.5 3" fill="none" stroke="#0d0d0d" stroke-width="1"/></svg>roheshkamdar@veltrane.com</li>
      <li><svg viewBox="0 0 12 12"><circle cx="6" cy="6" r="4.8" fill="none" stroke="#d9d9d9" stroke-width="1.2"/><path d="M1.2 6 H10.8 M6 1.2 C3.8 4 3.8 8 6 10.8 M6 1.2 C8.2 4 8.2 8 6 10.8" fill="none" stroke="#d9d9d9" stroke-width="1"/></svg>www.veltrane.com</li>
    </ul>
    <div class="wordmark">Veltrane<br>Group</div>
  </section>

  <section class="card card-back">
    <div class="wordmark">Veltrane<br>Group</div>
  </section>
</body>
</html>
```